"Velt Rover" Soil Conditioner for Lawn and Garden.

I need a product label with logo for a square 1 qt F Style plastic Bottle. The area would be 3.75" wide x 4.125" Tall front and back panel. Needs plenty of text area on the back panel.

Target Market(s)

Landscape and Garden

Industry/Entity Type

Home and Garden

Requirements
Must have
• Focus on the problems of heavy soils

```html
<!DOCTYPE html>
<html lang="en">
<head>
<meta charset="utf-8">
<title>Velt Rover Soil Conditioner Label</title>
<link rel="stylesheet" href="https://fonts.googleapis.com/css2?family=Bebas+Neue&family=Poppins:wght@400;600&display=swap">
<style>
  :root {
    --page-bg: #e9eaea;
    --forest-dark: #17301a;
    --forest-mid: #2c5128;
    --leaf-green: #8ed24c;
    --meadow-bottom: #55832c;
    --white: #ffffff;
    --tag-bg: #142a15;
  }
  * { margin: 0; padding: 0; box-sizing: border-box; }
  html, body {
    width: 900px; height: 1200px; overflow: hidden;
    background: var(--page-bg);
  }
  .label {
    position: absolute; left: 30px; top: 174px;
    width: 840px; height: 852px; overflow: hidden;
    background: var(--forest-dark);
    color: var(--white);
  }
  .label-photo {
    position: absolute; inset: 0;
    background:
      radial-gradient(ellipse 40% 45% at 66% 36%, rgba(120, 190, 70, 0.45), transparent 70%),
      linear-gradient(180deg, var(--forest-dark) 0%, var(--forest-mid) 45%, #2f4f2b 70%, var(--meadow-bottom) 100%);
  }
  .claim {
    position: absolute; left: 226px; top: 54px;
    display: flex; align-items: center; gap: 22px;
  }
  .claim-icon { width: 56px; height: 56px; }
  .claim-text {
    font-family: "Bebas Neue", sans-serif; font-size: 60px; line-height: 1;
    color: var(--white); letter-spacing: 0.5px;
  }
  .brand-top, .brand-bottom {
    position: absolute; font-family: "Bebas Neue", sans-serif; line-height: 0.8;
  }
  .brand-top { left: 264px; top: 244px; font-size: 184px; color: var(--white); }
  .brand-bottom { left: 206px; top: 384px; font-size: 184px; color: var(--leaf-green); }
  .subtitle {
    position: absolute; left: 0; width: 840px; text-align: center;
    font-family: "Bebas Neue", sans-serif; font-size: 46px; line-height: 1;
  }
  .subtitle-white { top: 540px; color: var(--white); padding-left: 60px; }
  .subtitle-green { top: 580px; color: var(--leaf-green); padding-left: 40px; }
  .tag {
    position: absolute; background: var(--tag-bg);
    font-family: "Bebas Neue", sans-serif; font-size: 17px; letter-spacing: 1px;
    padding: 3px 9px 1px; color: var(--white);
  }
  .body-copy {
    position: absolute; font-family: "Poppins", sans-serif; font-size: 13.5px;
    line-height: 16px; color: var(--white);
  }
  .usage-tag { left: 92px; top: 664px; }
  .usage-copy { left: 92px; top: 690px; width: 360px; }
  .instruction-tag { left: 92px; top: 743px; }
  .instruction-copy { left: 98px; top: 771px; width: 360px; }
  .divider {
    position: absolute; left: 507px; top: 688px; width: 1.5px; height: 100px;
    background: var(--tag-bg);
  }
  .caution-tag { left: 569px; top: 662px; }
  .caution-copy {
    position: absolute; left: 577px; top: 690px; width: 200px;
    font-family: "Poppins", sans-serif; font-weight: 600; font-size: 13.5px; line-height: 16px;
  }
  .volume {
    position: absolute; left: 569px; top: 740px; width: 195px; height: 58px;
    background: var(--tag-bg); display: flex; align-items: center; justify-content: center;
    font-family: "Bebas Neue", sans-serif; font-size: 26px; color: var(--leaf-green);
  }
</style>
</head>
<body>
  <section class="label">
    <div class="label-photo" role="img" aria-label="Close-up photo of a young green seedling sprouting from dark soil"></div>

    <div class="claim">
      <svg class="claim-icon" viewBox="0 0 56 56" aria-hidden="true">
        <circle cx="28" cy="28" r="24" fill="none" stroke="#8ed24c" stroke-width="6"/>
        <path d="M16 28 L26 38 L48 12" fill="none" stroke="#ffffff" stroke-width="6" stroke-linecap="round" stroke-linejoin="round"/>
      </svg>
      <span class="claim-text">100% Effective</span>
    </div>

    <h1>
      <span class="brand-top">VELT</span>
      <span class="brand-bottom">ROVER</span>
    </h1>

    <p class="subtitle subtitle-white">Soil Conditioner For</p>
    <p class="subtitle subtitle-green">Landscape And Garden:</p>

    <span class="tag usage-tag">Usages:</span>
    <p class="body-copy usage-copy">Promotes soil drainage and alleviates puddling and dry spots by opening more pore space for water and air on contact.</p>

    <span class="tag instruction-tag">Instruction:</span>
    <p class="body-copy instruction-copy">Lightly apply 1 oz./gal of water with a hose end sprayer, and then water in.</p>

    <div class="divider"></div>

    <span class="tag caution-tag">Caution:</span>
    <p class="caution-copy">KEEP OUT OF REACH OF CHILDREN!</p>

    <div class="volume">1 Quart (32 FL.OZ.)</div>
  </section>
</body>
</html>
```